New Business card design to reflect rebrand

I would like a business card design with a good base colour for our new logo and also a placeholder for a profile pic of the card holder. the design needs to be editable to the point that we can easily change the picture of the person and use that design for printmerlo etc. we are looking at a metalic finish business card so will need a good base colour to bring out the finish.

Target Market(s)

prospective customers

Industry/Entity Type

Business

Contact Information for Business Card

I would like one editable design that we can change the name of the card holder and profile picture. The design need to be in a format that be send to printmerlo etc.

Our address is Fenwick Lodge, Copse Lane, Ashcombe Vale, GU14 3TP Tel no. 01483 556172

Requirements
Must have
• place holder for a profile pic for the card holder. in AI or preferably PSD format

```html
<!DOCTYPE html>
<html lang="en">
<head>
<meta charset="utf-8">
<title>Corvane Workplace Services – Business Card</title>
<link rel="stylesheet" href="https://fonts.googleapis.com/css2?family=Michroma&family=Open+Sans:wght@400;600&display=swap">
<style>
  :root {
    --bg: #e6e6e6;
    --navy: #3e5573;
    --orange: #ee6300;
    --white: #ffffff;
    --photo-top: #56606f;
    --photo-bottom: #24263a;
  }
  * { box-sizing: border-box; margin: 0; padding: 0; }
  html, body {
    width: 1200px; height: 900px; overflow: hidden;
    background: var(--bg);
  }
  .canvas {
    position: relative; width: 1200px; height: 900px;
  }
  .card {
    position: absolute; left: 330px; width: 540px; height: 309px;
    overflow: hidden; box-shadow: 0 6px 18px rgba(0,0,0,.18);
  }
  .card--front {
    top: 110px; background: var(--navy);
    display: flex; align-items: center; justify-content: center;
  }
  .wordmark {
    font-family: "Michroma", sans-serif; color: var(--white);
    font-size: 22px; letter-spacing: 3px; text-transform: uppercase;
    text-align: center; line-height: 1.5;
  }
  .card--back { top: 480px; background: var(--navy); }
  .profile-photo {
    position: absolute; left: 12px; top: 58px; width: 262px; height: 251px;
    background: linear-gradient(180deg, var(--photo-top), var(--photo-bottom));
    border-radius: 120px 120px 0 0;
  }
  .info-panel {
    position: absolute; left: 280px; top: 38px; width: 260px; height: 271px;
    background: var(--orange); color: var(--white);
    padding: 48px 0 0 26px;
  }
  .info-panel__notch {
    position: absolute; left: -10px; top: 40px;
  }
  .holder-name {
    font-family: "Michroma", sans-serif; font-size: 13px;
    letter-spacing: 2px; text-transform: uppercase; font-weight: 400;
  }
  .contact-list {
    list-style: none; margin-top: 82px;
    font-family: "Open Sans", sans-serif; font-size: 12.5px; line-height: 1.45;
  }
  .contact-list li { display: flex; gap: 5px; }
  .contact-list svg { flex: none; margin-top: 4px; }
</style>
</head>
<body>
<main class="canvas">
  <section class="card card--front" aria-label="Card front">
    <p class="wordmark">Corvane<br>Workplace Services</p>
  </section>

  <section class="card card--back" aria-label="Card back">
    <div class="profile-photo" role="img" aria-label="Profile photo of the card holder"></div>
    <div class="info-panel">
      <svg class="info-panel__notch" width="10" height="18" viewBox="0 0 10 18" aria-hidden="true">
        <polygon points="10,0 0,9 10,18" fill="var(--orange)"/>
      </svg>
      <h1 class="holder-name">Daniel Hartwell</h1>
      <ul class="contact-list">
        <li>
          <svg width="10" height="10" viewBox="0 0 10 10" aria-hidden="true"><path d="M1 3c0-1 1-2 4-2s4 1 4 2v1H7V3H3v1H1z M2 5h6l1 4H1z" fill="#fff"/></svg>
          <span>01483 556172</span>
        </li>
        <li>
          <svg width="10" height="10" viewBox="0 0 10 10" aria-hidden="true"><rect x="0.5" y="2" width="9" height="6.5" fill="#fff"/><path d="M0.5 2l4.5 3.5L9.5 2" stroke="var(--orange)" fill="none"/></svg>
          <span>info@corvane.co.uk</span>
        </li>
        <li>
          <svg width="9" height="11" viewBox="0 0 9 11" aria-hidden="true"><path d="M4.5 0a4 4 0 0 1 4 4c0 3-4 7-4 7S.5 7 .5 4a4 4 0 0 1 4-4z" fill="#fff"/><circle cx="4.5" cy="4" r="1.5" fill="var(--orange)"/></svg>
          <span>Fenwick Lodge, Copse Lane<br>Ashcombe Vale, GU14 3TP</span>
        </li>
      </ul>
    </div>
  </section>
</main>
</body>
</html>
```